Cruise Booking Website

Cruise search and booking website

This project is a redesign of a cruise booking website we did a few years ago.

The current website is located here: http://voyage.pylonworks.example/en/

It's not fully functional but gives you ad idea how miserable the old design was.

All the information about cruises, cruise lines, destinations, ports and shore excursions will be similar to http://www.sailquest.example/
Actual search pages (form, results, single result, sailing and cabin selection, ship info, booking) will have EXACTLY the same info as sailquest.example

We like the style of http://harborfleetdesk.example, it's quite modern, good spacing, not overloaded with information. So you can use it as an example of what we like, not what we want as a final result for us. Please, don't copy it. The result should not be possible to resemble the harborfleetdesk.example, because our site has to be unique. This is important!
If you submit a design that clearly reminds another cruise site it will be rejected!

Also the mockup provided is just to give you the basic structure and show what information has to be present on the page. It doesn't mean the layout has to be the same as a mockup. The layout is up to the designer.

I've updated the mockup to be more generic so it doesn't confuse you:
https://files.boxvault.example/s/k7m2qp9wz4hx/Home%20page.png

When you're adding social sharing icons like plazanet/chirpline you have to use chinese ones instead:
https://files.boxvault.example/s/t3nr8vx5lc2e/chinese-social-icons.png
Originals: http://minilk.example/qR7t

We'll start with home page first and after it's approved inner pages can be designed.

I know the cost of the project doesn't look high, but the task is straight forward and doesn't require to be very original, it's better to follow existing design and layout patterns that proved to work well.
That's why I encourage you to choose a template to build the design on top of one of https://themeparlor.example/ themes if it will save the design work, will be easier and faster for you. So it will be more like a customization than a new design from scratch.

Mockups, site map and logo files:
- https://files.boxvault.example/sh/h48dm2rs73fkpw/QvnbW2Xz8e

Website tree:
- https://sheets.papernest.example/document/d/7xPqR2mLw9sTk4VbN8cHj3YzA6eUf5GdKo1iMnBv/edit?usp=sharing
Updates

So far a lot of designs are just copying http://www.harborfleetdesk.example/ - we don't like it!

We like the style of harborfleetdesk.example, it's quite modern, good spacing, not overloaded with information. So you can use it as an example of what we like, not what we want as a final result for us. Please, don't copy it. The result should not be possible to resemble the harborfleetdesk.example, because our site has to be unique. This is important!

Target Market(s)

Chinese travellers

Industry/Entity Type

Build

Requirements
Must have
• * White, blue and red
* Large spacing, not too much information cramped into a small space like sailquest.example or the current website
* More "hidden" info in popups, tabs and so on, so not to many things are visible at the same time
* Compatible with kestrel scaffold styling (for easier coding):
- http://kestrelkit.codeshelf.example/scaffold/index.html
- http://skinmarket.example/
* Feel free to propose to build the design on top of one of https://themeparlor.example/ themes if it will save the design work, will be easier and faster for you

```html
<!DOCTYPE html>
<html lang="en">
<head>
<meta charset="utf-8">
<title>航星邮轮 – Cruise Booking</title>
<link href="https://fonts.googleapis.com/css2?family=Open+Sans:wght@300;400;600;700&display=swap" rel="stylesheet">
<style>
:root{
  --blue:#1f73b7;
  --blue-dark:#195c94;
  --sky:#4eb0ee;
  --red:#e2483b;
  --red-dark:#c93a2e;
  --grey:#ececec;
  --grey-line:#d6d6d6;
  --text:#333;
  --muted:#777;
  --white:#fff;
}
*{box-sizing:border-box;margin:0;padding:0}
html,body{width:817px;height:1200px;overflow:hidden}
body{font-family:"Open Sans",Arial,sans-serif;color:var(--text);background:var(--white);position:relative}
.abs{position:absolute}

/* header */
.site-header{left:0;top:0;width:817px;height:61px;background:var(--blue)}
.brand{left:32px;top:12px;display:flex;align-items:center;gap:8px;color:var(--white);font-weight:700;font-size:30px;letter-spacing:-1px}
.brand-dot{width:32px;height:32px;border-radius:50%;background:var(--sky);border:2px solid var(--white)}
.header-block{top:11px;color:var(--white)}
.header-block h4{font-size:10.5px;font-weight:400;letter-spacing:1px;text-transform:uppercase;border-bottom:1px solid rgba(255,255,255,.7);padding-bottom:2px;width:112px}
.header-block p{font-size:8.5px;margin-top:5px}
.dest-select{margin-top:4px;width:134px;height:13px;background:var(--white);color:var(--text);font-size:7.5px;padding:1px 4px;position:relative}
.dest-select::after{content:"";position:absolute;right:2px;top:1px;width:11px;height:11px;background:var(--blue-dark)}

.main-nav{left:30px;top:61px;width:757px;height:29px;background:var(--grey);display:flex;align-items:center;padding-left:11px;gap:13px}
.main-nav span{font-size:10.3px;text-transform:uppercase;color:#222}
.main-nav span::after{content:"⌄";color:var(--red);margin-left:3px;font-size:9px;position:relative;top:-2px}

/* hero */
.hero{left:0;top:90px;width:817px;height:260px;background:linear-gradient(180deg,#2a6aa2 0%,#3c7fb8 45%,#245b8c 100%)}
.hero-edge{left:0;top:350px;width:817px;height:2px;background:var(--red)}
.hero-title{left:121px;top:135px;color:var(--white);font-weight:300;font-size:28px;letter-spacing:.5px}
.hero-title b{font-weight:700;color:#1e2d3a;font-size:33px}
.hero-copy{left:121px;top:184px;width:311px;background:var(--blue);color:var(--white);font-size:9.6px;line-height:16.5px;padding:4px 8px}
.hero-photo{left:495px;top:124px;width:180px;height:179px;border:3px solid var(--white);background:linear-gradient(160deg,#e9e6df,#c9b79a 55%,#6d7f90);box-shadow:0 2px 6px rgba(0,0,0,.3)}
.value-badge{left:477px;top:253px;width:62px;height:62px;border-radius:50%;background:var(--white);border:3px solid var(--white);overflow:hidden;box-shadow:0 2px 4px rgba(0,0,0,.3);text-align:center;transform:rotate(12deg)}
.value-badge span{position:relative;z-index:1;display:block;font-weight:700;line-height:12px}
.value-badge .best{color:var(--red);font-size:12px;margin-top:9px}
.value-badge .value{color:var(--text);font-size:8.5px;margin-top:1px}
.value-badge::after{content:"";position:absolute;left:0;bottom:0;width:100%;height:16px;background:var(--red)}
.hero-arrow{top:178px;width:26px;height:56px;background:rgba(20,60,110,.6);display:flex;align-items:center;justify-content:center}

/* utility bar */
.hotline{left:45px;top:358px;width:182px;height:38px;border:1px solid var(--blue);display:flex;align-items:center;gap:8px;padding-left:7px}
.hotline dl{font-size:10px;line-height:15px;display:grid;grid-template-columns:40px auto}
.hotline dd{color:var(--blue-dark);font-size:13.5px}
.btn-blue{top:366px;width:106px;height:25px;background:var(--sky);color:#1d3d5c;font-size:9.5px;font-weight:600;display:flex;align-items:center;gap:7px;padding-left:5px}
.btn-blue i{width:17px;height:17px;border:2px solid var(--red);display:block;border-radius:2px}
.search-box{left:617px;top:366px;width:170px;height:44px;background:var(--grey)}
.search-box .field{position:absolute;left:8px;top:6px;width:117px;height:13px;border:1px solid #999;border-radius:7px;background:var(--white)}
.search-box .go{position:absolute;left:133px;top:3px;font-size:12px;color:var(--blue-dark)}
.search-box .adv{position:absolute;left:8px;top:25px;font-size:9px;color:var(--blue-dark);text-decoration:underline}

/* feature cards */
.feature{top:412px;width:175px;height:144px;background:var(--grey)}
.feature .pic{height:94px}
.feature h3{font-size:11.3px;font-weight:400;margin:10px 0 3px 9px}
.read-more{margin-left:9px;display:inline-flex;align-items:center;background:var(--white);font-size:8.3px;font-weight:700;color:var(--red);height:13px;padding-right:8px}
.read-more::before{content:"+";width:13px;height:13px;background:var(--red);color:var(--white);display:flex;align-items:center;justify-content:center;margin-right:6px;font-size:11px}

/* intro columns */
.intro-icon{top:587px;width:78px;height:78px;border:1.5px solid var(--red);border-radius:50%;display:flex;align-items:center;justify-content:center}
.intro{top:677px;width:210px}
.intro h3{font-size:13px;font-weight:400;color:#222;margin-bottom:6px}
.intro p{font-size:9.2px;line-height:11.6px;color:var(--muted)}
.intro a{color:var(--red);text-decoration:none}
.rule{left:30px;top:772px;width:757px;height:1px;background:var(--red)}
.section-title{left:30px;top:779px;font-size:23px;font-weight:300;color:#555}

/* deals */
.deal{top:810px;width:186px;height:183px;background:var(--grey);padding:0 3px}
.deal.tall{height:193px}
.deal-head{margin-top:19px;height:36px;background:var(--sky);color:var(--white);font-size:15px;font-weight:300;display:flex;align-items:center;justify-content:center}
.deal.tall .deal-head{height:48px;background:var(--blue);font-size:15.5px}
.deal-body{background:var(--white);height:124px;padding-top:8px;text-align:center}
.deal.tall .deal-body{background:transparent;height:auto}
.choose{display:inline-block;background:var(--red);color:var(--white);font-size:8px;font-weight:700;letter-spacing:.5px;padding:3px 11px}
.cruise-list{list-style:none;font-size:8.6px;text-align:left;padding:6px 5px 0 6px}
.cruise-list li{display:flex;justify-content:space-between;line-height:15.3px}
.brand-word{font-size:14px;color:var(--blue);letter-spacing:.5px}
.honey{display:flex;justify-content:space-around;padding:0 8px}
.honey div{width:66px;font-size:8px;text-align:center;line-height:9px}
.honey .ph{width:54px;height:54px;margin:0 auto 8px;border:2px solid var(--sky);background:linear-gradient(160deg,#bfe2f4,#e9eef2 55%,#7fb5d5)}

/* clients */
.clients{left:0;top:1030px;width:817px;height:55px;background:var(--red);color:var(--white)}
.clients h2{position:absolute;left:35px;top:11px;font-size:20px;font-weight:300}
.client-row{position:absolute;left:270px;top:0;height:55px;width:520px;display:flex;align-items:center;justify-content:space-between;font-size:12px;font-weight:600}

/* footer */
.site-footer{left:0;top:1085px;width:817px;height:115px;background:var(--sky);color:#12314d}
.foot-col{position:absolute;top:10px;list-style:none;font-size:8.5px;line-height:14.2px}
.foot-col li::before{content:"";display:inline-block;width:4px;height:4px;background:var(--white);margin-right:6px;vertical-align:2px}
.social{position:absolute;top:17px;display:flex;align-items:center;gap:7px;font-size:10.5px}
.social i{width:17px;height:17px;border:2px solid var(--red);background:var(--white);display:block}
.foot-rule{position:absolute;left:30px;top:79px;width:757px;height:1px;background:#2d6f9e}
.copyright{position:absolute;left:0;top:85px;width:817px;text-align:center;font-size:8.5px;line-height:14px}
</style>
</head>
<body>

<header class="site-header abs">
  <div class="brand abs"><span class="brand-dot"></span>航星邮轮</div>
  <div class="header-block abs" style="left:492px">
    <h4>Booking Details</h4>
    <p>Book online or call</p>
  </div>
  <div class="header-block abs" style="left:635px">
    <h4>Find Your Cruise</h4>
    <div class="dest-select">Popular Destinations</div>
  </div>
</header>

<nav class="main-nav abs">
  <span>Cruise Info</span><span>Destinations</span><span>Cruise Lines</span><span>Cruise Deals</span><span>Cruise Ports</span><span>Shore Excursions</span><span>Blog</span><span>FAQ</span><span>Contact Us</span>
</nav>

<section class="hero abs" role="img" aria-label="Open sea seen from a cruise ship deck"></section>
<div class="hero-edge abs"></div>
<div class="hero-arrow abs" style="left:30px"><svg width="10" height="16"><path d="M8 2 2 8l6 6" fill="none" stroke="#fff" stroke-width="2"/></svg></div>
<div class="hero-arrow abs" style="left:762px"><svg width="10" height="16"><path d="M2 2l6 6-6 6" fill="none" stroke="#fff" stroke-width="2"/></svg></div>
<h1 class="hero-title abs">WELCOME TO <b>航星邮轮</b></h1>
<p class="hero-copy abs">Cruises are offered throughout the world and for each destination there are a number of cruise lines to choose from. From contemporary cruise lines to luxury cruise lines each cruise line offers different itineraries, features and options.</p>
<div class="hero-photo abs" role="img" aria-label="Couple walking along a sunny cruise ship deck"></div>
<div class="value-badge abs"><span class="best">BEST</span><span class="value">VALUE</span></div>

<div class="hotline abs">
  <svg width="20" height="28" viewBox="0 0 20 28"><path d="M4 2h5l2 7-4 2c1 4 3 7 6 9l3-3 4 4-3 5C8 27 1 16 1 5z" fill="#e2483b"/></svg>
  <dl><dt>Hotline:</dt><dd>4000 123 456</dd><dt>Book:</dt><dd>010-5555 0199</dd></dl>
</div>
<div class="btn-blue abs" style="left:389px"><i></i>REGISTER</div>
<div class="btn-blue abs" style="left:504px"><i></i>MY ACCOUNT</div>
<div class="search-box abs"><span class="field"></span><span class="go">Search</span><span class="adv">Advance Search</span></div>

<article class="feature abs" style="left:30px"><div class="pic" role="img" aria-label="Diver over a coral reef" style="background:linear-gradient(160deg,#2d6d93,#4d8fb0 50%,#7a5a55)"></div><h3>Packages</h3><span class="read-more">Read More</span></article>
<article class="feature abs" style="left:224px"><div class="pic" role="img" aria-label="Cruise ship sailing at sea" style="background:linear-gradient(170deg,#6aa9d8,#2f72ad 55%,#1f4f80)"></div><h3>Cruise lines</h3><span class="read-more">Read More</span></article>
<article class="feature abs" style="left:418px"><div class="pic" role="img" aria-label="Rocky shoreline with surf" style="background:linear-gradient(170deg,#9cc6e6,#3d7fa8 50%,#8a7a62)"></div><h3>Shores</h3><span class="read-more">Read More</span></article>
<article class="feature abs" style="left:613px"><div class="pic" role="img" aria-label="Ship theatre interior with chandeliers" style="background:linear-gradient(170deg,#5a4a3a,#c8a46a 45%,#4a3a30)"></div><h3>Cruise news</h3><span class="read-more">Read More</span></article>

<div class="intro-icon abs" style="left:111px"><svg width="34" height="46" viewBox="0 0 34 46" fill="none" stroke="#e2483b" stroke-width="2"><rect x="10" y="4" width="14" height="24" rx="7"/><path d="M5 20c0 8 5 13 12 13s12-5 12-13M17 33v8M11 42h12"/></svg></div>
<div class="intro-icon abs" style="left:369px"><svg width="48" height="34" viewBox="0 0 48 34" fill="#e2483b"><circle cx="17" cy="9" r="8"/><circle cx="32" cy="9" r="8"/><path d="M1 33c0-10 7-15 16-15s16 5 16 15zM22 33c1-9 3-13 10-15 9 0 15 5 15 15z"/></svg></div>
<div class="intro-icon abs" style="left:628px"><svg width="34" height="44" viewBox="0 0 34 44" fill="none" stroke="#e2483b" stroke-width="2.5"><circle cx="17" cy="27" r="13"/><path d="M14 4h6M17 4v10M17 27l4-6"/></svg></div>

<div class="intro abs" style="left:42px"><h3>Promotions</h3><p>hangxingcruise.example offers the best cruise deals and discounts on all cruise lines and cruise vacation packages worldwide. Get last minute cruise deals, regional and resident specials and receive special amenities, <a>Learn More &gt;</a></p></div>
<div class="intro abs" style="left:301px"><h3>First Time Cruisers</h3><p>Let us put your mind at ease by answering questions about tickets, tipping, documentation, dress codes and more. How to prepare before your cruise and advice for after the cruise is outlined. <a>Learn More &gt;</a></p></div>
<div class="intro abs" style="left:559px"><h3>Last Minute Deals</h3><p>Last minute cruises offer a great opportunity to get exceptional cruise deals, discounts, upgrades and other valuable offers on itineraries that cruise lines are looking to fill for close in departures. <a>Learn More &gt;</a></p></div>

<div class="rule abs"></div>
<h2 class="section-title abs">Our Deals</h2>

<section class="deal abs" style="left:30px">
  <div class="deal-head">Deal of the Day</div>
  <div class="deal-body">
    <div class="brand-word" style="margin-top:12px">CROWNWAVE CRUISES</div>
    <div style="font-size:15px;margin:14px 0 13px">For $299</div>
    <span class="choose">CHOOSE PLAN</span>
  </div>
</section>
<section class="deal tall abs" style="left:218px">
  <div class="deal-head">Featured Cruise Deals</div>
  <div class="deal-body">
    <ul class="cruise-list">
      <li><span>3 Day Bahamas • Meridian Aurora</span><span>$209</span></li>
      <li><span>7 Day Alaska • Nordvik Sun</span><span>$209</span></li>
      <li><span>7 Day Alaska • Sapphire Crown</span><span>$209</span></li>
      <li><span>5 Day Caribbean • Nordvik Pearl</span><span>$209</span></li>
      <li><span>7 Day Alaska • ms Havenhold</span><span>$209</span></li>
    </ul>
    <span class="choose" style="margin-top:6px">CHOOSE PLAN</span>
  </div>
</section>
<section class="deal tall abs" style="left:407px">
  <div class="deal-head">Exceptional Cruise Offers</div>
  <div class="deal-body" style="text-align:left;padding-left:9px">
    <div class="brand-word" style="font-size:12px">Castellan</div>
    <p style="font-size:8.6px;line-height:14px;margin:8px 0 0 18px"><b style="font-weight:600">Castellan Cruises</b> <span style="color:var(--red)">EXCLUSIVE RATES</span><br>All Inclusive Beverage Package • Kids<br>Free on select Europe sailings</p>
    <div style="text-align:center;margin-top:21px;padding-right:9px"><span class="choose">CHOOSE PLAN</span></div>
  </div>
</section>
<section class="deal abs" style="left:597px">
  <div class="deal-head">Honeymoon Cruises</div>
  <div class="deal-body">
    <div class="honey">
      <div><div class="ph" role="img" aria-label="Wedding couple by the sea"></div>HONEYMOON 1</div>
      <div><div class="ph" role="img" aria-label="Couple on a tropical beach"></div>BOOKING NOTES 1</div>
    </div>
    <span class="choose" style="margin-top:6px">CHOOSE PLAN</span>
  </div>
</section>

<section class="clients abs">
  <h2>Some Of Our Clients</h2>
  <div class="client-row">
    <span>‹</span><span>NORDVIK LINE</span><span>Castellan</span><span>CROWNWAVE</span><span>Starlit Cruise Line</span><span>MERIDIAN SEA</span><span>›</span>
  </div>
</section>

<footer class="site-footer abs">
  <ul class="foot-col" style="left:52px"><li>About us</li><li>Contact us</li><li>Reward Points</li><li>Payment info</li></ul>
  <ul class="foot-col" style="left:227px"><li>Terms of service</li><li>Terms of insurance</li><li>Cooperation network</li><li>Registration agreement</li></ul>
  <ul class="foot-col" style="left:408px"><li>Cruise promotion policy</li><li>Booking process explanation</li><li>Bonus points collection policy</li></ul>
  <div class="social" style="left:609px"><i></i>Plazanet</div>
  <div class="social" style="left:689px"><i></i>Linkplace</div>
  <div class="social" style="left:609px;top:43px"><i></i>Chirpline</div>
  <div class="social" style="left:689px;top:43px"><i></i>Searchbeam</div>
  <div class="foot-rule"></div>
  <p class="copyright">Copyright © 2011 航星邮轮网 版权所有<br>京ICP备 00000000号</p>
</footer>

</body>
</html>
```